Website for software company "velora"

We need a website for our software company/startup named "velora". We are developing several products (currently 3 standard-software products) which are all in different sectors, but all our products are available for Laptops/PC/Mobile Phones/Tablets, ... We do also create custom software and support our customers with consulting to optimize their processes.
We already have a Logo which you can find in the attached files.
We are a young team of 4 members (two founders and 2 employees).

To get an idea of our products -> the first one is a planning software for healthcare organizations (eg. BlueHaven, firebrigade, pharmacy), the second one is a booking software for sport clubs and the third one is a competition software for sports hunting. You see very diverse. Include or ignore this info of our products as you like.

The design has to be a bootstrap 4 (or higher) design. We have licenced FontAwesome as iconset. Responsive design should come without saying.

• Starting page, product pages, news section, contact, team, services

```html
<!DOCTYPE html>
<html lang="en">
<head>
<meta charset="utf-8">
<title>velora — Hero Banners</title>
<link href="https://fonts.googleapis.com/css2?family=Montserrat:wght@300;400;500;600;700;800&display=swap" rel="stylesheet">
<style>
:root{
  --orange:#f37521;
  --navy:#222c3b;
  --navy-deep:#1b2431;
  --ink:#1f2530;
  --light:#eef0f5;
  --white:#ffffff;
  --muted:#8b93a3;
  --blue:#4657d6;
  --green:#33c27a;
  --purple:#7a5cf5;
}
*{margin:0;padding:0;box-sizing:border-box}
html,body{width:1200px;height:5004px;overflow:hidden;background:var(--white);font-family:'Montserrat',sans-serif}
.page{position:relative;width:1200px;height:5004px}
.page-title{position:absolute;top:112px;left:0;width:1200px;text-align:center;font-size:80px;font-weight:800;letter-spacing:2px;color:#111}
.banner{position:absolute;left:0;width:1200px;overflow:hidden}
.abs{position:absolute}
.nav{position:absolute;left:125px;right:115px;display:flex;align-items:center}
.brand{display:flex;align-items:center;gap:10px;width:295px;font-size:44px;font-weight:700;letter-spacing:1px;color:var(--white)}
.brand-mark{width:14px;height:14px;background:var(--orange)}
.menu{display:flex;gap:58px;font-size:12px;font-weight:500;color:var(--white)}
.menu .active{color:var(--orange);font-weight:600;padding-bottom:8px;border-bottom:2px solid var(--orange)}
.cta{margin-left:auto;font-size:12px;font-weight:500;color:var(--white);border:1.5px solid var(--white);padding:10px 32px}
.cta.pill{border-radius:20px}
.cta.solid{background:var(--navy);border-color:var(--navy)}
.cta.accent{border-color:var(--orange)}
.theme-light .brand{color:var(--ink)}
.theme-light .menu{color:#6b7280}
.nav-rule{position:absolute;left:0;right:0;height:1px;background:rgba(255,255,255,.12)}
.eyebrow{font-size:17px;font-weight:500;color:var(--orange);letter-spacing:.3px}
.h-light{font-size:31px;font-weight:300;color:var(--white);line-height:1.2}
.h-bold{font-size:38px;font-weight:700;color:var(--white);line-height:1.1}
.theme-light .h-light,.theme-light .h-bold{color:var(--ink)}
.lede{font-size:15px;font-weight:400;color:#c9ced8;line-height:1.45}
.theme-light .lede{color:#5b6270}
.btn{display:inline-block;background:var(--orange);color:var(--white);font-size:13px;font-weight:600;text-align:center}
.shot{position:absolute;background:var(--white);border-radius:6px;box-shadow:0 10px 30px rgba(0,0,0,.25);overflow:hidden}
.shot svg{display:block;width:100%;height:100%}
</style>
</head>
<body>
<div class="page">

<svg width="0" height="0" style="position:absolute" aria-hidden="true">
  <defs>
    <symbol id="bars" viewBox="0 0 200 80">
      <g>
        <rect x="4" y="40" width="5" height="40" fill="#4657d6"/><rect x="11" y="55" width="5" height="25" fill="#33c27a"/>
        <rect x="24" y="30" width="5" height="50" fill="#4657d6"/><rect x="31" y="48" width="5" height="32" fill="#7a5cf5"/>
        <rect x="44" y="20" width="5" height="60" fill="#33c27a"/><rect x="51" y="38" width="5" height="42" fill="#4657d6"/>
        <rect x="64" y="50" width="5" height="30" fill="#7a5cf5"/><rect x="71" y="28" width="5" height="52" fill="#4657d6"/>
        <rect x="84" y="15" width="5" height="65" fill="#4657d6"/><rect x="91" y="35" width="5" height="45" fill="#33c27a"/>
        <rect x="104" y="42" width="5" height="38" fill="#7a5cf5"/><rect x="111" y="22" width="5" height="58" fill="#4657d6"/>
        <rect x="124" y="10" width="5" height="70" fill="#33c27a"/><rect x="131" y="30" width="5" height="50" fill="#4657d6"/>
        <rect x="144" y="36" width="5" height="44" fill="#4657d6"/><rect x="151" y="52" width="5" height="28" fill="#7a5cf5"/>
        <rect x="164" y="18" width="5" height="62" fill="#4657d6"/><rect x="171" y="40" width="5" height="40" fill="#33c27a"/>
        <rect x="184" y="26" width="5" height="54" fill="#7a5cf5"/><rect x="191" y="44" width="5" height="36" fill="#4657d6"/>
      </g>
    </symbol>

    <symbol id="dash-overview" viewBox="0 0 435 340">
      <rect width="435" height="340" fill="#f6f7fb"/>
      <text x="10" y="36" font-family="Montserrat,sans-serif" font-size="12" font-weight="600" fill="#1f2530">Overview</text>
      <rect x="8" y="46" width="240" height="130" rx="3" fill="#fff" stroke="#e6e9f0"/>
      <text x="16" y="60" font-family="Montserrat,sans-serif" font-size="6" fill="#8b93a3">Average Charts</text>
      <use href="#bars" x="18" y="75" width="220" height="85"/>
      <line x1="18" y1="160" x2="238" y2="160" stroke="#e6e9f0"/>
      <rect x="256" y="46" width="171" height="130" rx="3" fill="#fff" stroke="#e6e9f0"/>
      <text x="264" y="60" font-family="Montserrat,sans-serif" font-size="6" fill="#8b93a3">Calculation</text>
      <text x="272" y="95" font-family="Montserrat,sans-serif" font-size="16" font-weight="700" fill="#4657d6">$</text>
      <path d="M339 82 v12 M334 90 l5 5 l5 -5" stroke="#4657d6" stroke-width="2.5" fill="none"/>
      <path d="M402 80 l3 7 7 1 -5 5 1 7 -6 -3 -6 3 1 -7 -5 -5 7 -1z" fill="#7a5cf5"/>
      <text x="264" y="115" font-family="Montserrat,sans-serif" font-size="7" font-weight="600" fill="#33c27a">$ 5.124</text>
      <text x="322" y="115" font-family="Montserrat,sans-serif" font-size="7" font-weight="600" fill="#33c27a">1.340.230</text>
      <text x="390" y="115" font-family="Montserrat,sans-serif" font-size="7" font-weight="600" fill="#33c27a">135.020</text>
      <rect x="264" y="135" width="155" height="3" fill="#e6e9f0"/><rect x="264" y="135" width="90" height="3" fill="#4657d6"/>
      <rect x="264" y="148" width="155" height="3" fill="#e6e9f0"/><rect x="264" y="148" width="120" height="3" fill="#33c27a"/>
      <rect x="264" y="161" width="155" height="3" fill="#e6e9f0"/><rect x="264" y="161" width="60" height="3" fill="#7a5cf5"/>
      <rect x="8" y="184" width="240" height="148" rx="3" fill="#fff" stroke="#e6e9f0"/>
      <text x="16" y="198" font-family="Montserrat,sans-serif" font-size="6" fill="#8b93a3">Maps</text>
      <g role="img" aria-label="World map with location markers"><rect x="20" y="206" width="216" height="112" rx="4" fill="#e9ecf3"/></g>
      <rect x="256" y="184" width="171" height="148" rx="3" fill="#fff" stroke="#e6e9f0"/>
      <text x="264" y="198" font-family="Montserrat,sans-serif" font-size="6" fill="#8b93a3">Analytical</text>
      <g fill="#4657d6">
        <rect x="264" y="210" width="90" height="3"/><rect x="264" y="222" width="70" height="3"/><rect x="264" y="234" width="100" height="3"/>
        <rect x="264" y="246" width="55" height="3"/><rect x="264" y="258" width="85" height="3"/><rect x="264" y="270" width="65" height="3"/>
      </g>
      <circle cx="405" cy="220" r="10" fill="none" stroke="#4657d6" stroke-width="3"/>
      <circle cx="405" cy="252" r="10" fill="none" stroke="#4657d6" stroke-width="3"/>
      <circle cx="405" cy="284" r="10" fill="none" stroke="#4657d6" stroke-width="3"/>
      <rect x="264" y="300" width="60" height="3" fill="#f37521"/><rect x="330" y="300" width="60" height="3" fill="#e6e9f0"/>
    </symbol>

    <symbol id="side-left" viewBox="0 0 150 285">
      <rect width="150" height="285" fill="#fff"/>
      <rect width="150" height="16" fill="#222c3b"/>
      <polyline points="10,50 30,40 50,48 70,32 90,44 110,36 140,46" fill="none" stroke="#f37521" stroke-width="1.5"/>
      <polyline points="10,58 30,54 50,60 70,52 90,58 110,50 140,56" fill="none" stroke="#4657d6" stroke-width="1"/>
      <rect x="6" y="86" width="66" height="70" fill="#fff" stroke="#e6e9f0"/>
      <text x="12" y="98" font-family="Montserrat,sans-serif" font-size="5" fill="#8b93a3">Lorem ipsum</text>
      <circle cx="39" cy="125" r="15" fill="none" stroke="#e6e9f0" stroke-width="5"/>
      <path d="M39 110 a15 15 0 1 1 -14 20" fill="none" stroke="#33c27a" stroke-width="5"/>
      <rect x="78" y="86" width="66" height="70" fill="#fff" stroke="#e6e9f0"/>
      <text x="84" y="98" font-family="Montserrat,sans-serif" font-size="5" fill="#8b93a3">Lorem ipsum</text>
      <polyline points="84,140 96,128 108,134 120,118 138,112" fill="none" stroke="#4657d6" stroke-width="1.2"/>
      <rect x="84" y="145" width="54" height="6" fill="#4657d6"/>
      <rect x="6" y="164" width="138" height="52" fill="#fff" stroke="#e6e9f0"/>
      <text x="12" y="176" font-family="Montserrat,sans-serif" font-size="5" fill="#8b93a3">Lorem ipsum</text>
      <rect x="6" y="224" width="138" height="55" fill="#fff" stroke="#e6e9f0"/>
      <rect x="14" y="236" width="80" height="3" fill="#33c27a"/><rect x="14" y="248" width="100" height="3" fill="#f37521"/>
      <rect x="14" y="260" width="60" height="3" fill="#4657d6"/>
    </symbol>

    <symbol id="side-right" viewBox="0 0 135 285">
      <rect width="135" height="285" fill="#fff"/>
      <rect width="135" height="16" fill="#222c3b"/>
      <text x="50" y="30" font-family="Montserrat,sans-serif" font-size="5" fill="#8b93a3">Lorem ipsum</text>
      <g fill="#f37521"><rect x="100" y="40" width="14" height="5" rx="2"/><rect x="100" y="52" width="14" height="5" rx="2"/><rect x="100" y="64" width="14" height="5" rx="2"/><rect x="100" y="76" width="14" height="5" rx="2"/><rect x="100" y="88" width="14" height="5" rx="2"/></g>
      <g fill="#e6e9f0"><rect x="50" y="41" width="40" height="3"/><rect x="50" y="53" width="40" height="3"/><rect x="50" y="65" width="40" height="3"/><rect x="50" y="77" width="40" height="3"/><rect x="50" y="89" width="40" height="3"/></g>
      <use href="#bars" x="50" y="140" width="80" height="60"/>
      <circle cx="25" cy="260" r="12" fill="none" stroke="#e6e9f0" stroke-width="4"/>
      <path d="M25 248 a12 12 0 0 1 10 18" fill="none" stroke="#4657d6" stroke-width="4"/>
      <rect x="50" y="252" width="70" height="3" fill="#e6e9f0"/>
    </symbol>

    <symbol id="phone-booking" viewBox="0 0 175 355">
      <rect x="1" y="1" width="173" height="353" rx="16" fill="#fff" stroke="#dfe3ea" stroke-width="2"/>
      <path d="M1 17 a16 16 0 0 1 16 -16 h141 a16 16 0 0 1 16 16 v115 h-173z" fill="#3f86d9"/>
      <text x="14" y="28" font-family="Montserrat,sans-serif" font-size="9" font-weight="600" fill="#fff">From:</text>
      <text x="92" y="28" font-family="Montserrat,sans-serif" font-size="9" font-weight="600" fill="#fff">To:</text>
      <rect x="14" y="38" width="70" height="16" rx="3" fill="#2f6fbe"/><text x="20" y="49" font-family="Montserrat,sans-serif" font-size="7" fill="#fff">Dublin</text>
      <rect x="92" y="38" width="70" height="16" rx="3" fill="#2f6fbe"/><text x="98" y="49" font-family="Montserrat,sans-serif" font-size="7" fill="#fff">Belfast</text>
      <text x="14" y="80" font-family="Montserrat,sans-serif" font-size="9" font-weight="600" fill="#fff">Date:</text>
      <rect x="14" y="90" width="148" height="18" rx="3" fill="#2f6fbe"/><text x="62" y="102" font-family="Montserrat,sans-serif" font-size="7" fill="#fff">30.04.19</text>
      <text x="14" y="156" font-family="Montserrat,sans-serif" font-size="9" font-weight="600" fill="#1f2530">Choose Outbound</text>
      <g font-family="Montserrat,sans-serif" font-size="8" font-weight="600" fill="#1f2530">
        <text x="14" y="186">9:30</text><text x="60" y="186">11:11</text><text x="14" y="198">Dublin</text><text x="60" y="198">Belfast</text>
        <text x="14" y="242">10:42</text><text x="60" y="242">12:56</text><text x="14" y="254">Dublin</text><text x="60" y="254">Belfast</text>
        <text x="14" y="298">13:30</text><text x="60" y="298">15:35</text><text x="14" y="310">Dublin</text><text x="60" y="310">Belfast</text>
      </g>
      <rect x="124" y="184" width="38" height="16" rx="3" fill="#33c27a"/><text x="131" y="195" font-family="Montserrat,sans-serif" font-size="7.5" font-weight="600" fill="#fff">$35.4</text>
      <rect x="124" y="240" width="38" height="16" rx="3" fill="#33c27a"/><text x="131" y="251" font-family="Montserrat,sans-serif" font-size="7.5" font-weight="600" fill="#fff">$26.5</text>
      <rect x="124" y="296" width="38" height="16" rx="3" fill="#fff" stroke="#dfe3ea"/><text x="131" y="307" font-family="Montserrat,sans-serif" font-size="7.5" font-weight="600" fill="#1f2530">$37.8</text>
      <circle cx="28" cy="340" r="5" fill="#33c27a"/><circle cx="88" cy="340" r="5" fill="#dfe3ea"/><circle cx="148" cy="340" r="5" fill="#dfe3ea"/>
    </symbol>

    <symbol id="phone-wallet" viewBox="0 0 180 305">
      <rect x="1" y="1" width="178" height="303" rx="14" fill="#fff" stroke="#dfe3ea" stroke-width="2"/>
      <text x="16" y="20" font-family="Montserrat,sans-serif" font-size="6" font-weight="600" fill="#1f2530">9:41</text>
      <text x="90" y="46" text-anchor="middle" font-family="Montserrat,sans-serif" font-size="10" font-weight="600" fill="#1f2530">Wallets</text>
      <rect x="12" y="60" width="156" height="62" rx="6" fill="#f6f7fb"/>
      <circle cx="26" cy="76" r="6" fill="#1f2530"/>
      <text x="38" y="78" font-family="Montserrat,sans-serif" font-size="5" fill="#8b93a3">Total Wallet Balance</text>
      <text x="22" y="102" font-family="Montserrat,sans-serif" font-size="15" font-weight="700" fill="#1f2530">$39.584</text>
      <rect x="124" y="92" width="34" height="11" rx="5" fill="#33c27a"/><text x="131" y="100" font-family="Montserrat,sans-serif" font-size="5.5" font-weight="600" fill="#fff">+2.08%</text>
      <g font-family="Montserrat,sans-serif" font-size="5.5" fill="#1f2530">
        <circle cx="26" cy="160" r="8" fill="#f5a623"/><text x="42" y="158">3.529020 NRX</text><text x="130" y="158">$18,153</text>
        <circle cx="26" cy="200" r="8" fill="#7a5cf5"/><text x="42" y="198">12.83285 QLT</text><text x="130" y="198">$4,822</text>
        <circle cx="26" cy="240" r="8" fill="#3f86d9"/><text x="42" y="238">197.0240 ZPH</text><text x="130" y="238">$650</text>
      </g>
      <g fill="#33c27a" font-family="Montserrat,sans-serif" font-size="5"><text x="130" y="167">+4.32%</text><text x="130" y="207">+2.01%</text></g>
      <text x="130" y="247" fill="#e0474c" font-family="Montserrat,sans-serif" font-size="5">-1.05%</text>
    </symbol>

    <symbol id="dash-report" viewBox="0 0 480 375">
      <rect width="480" height="375" fill="#f1f4fb"/>
      <text x="30" y="38" font-family="Montserrat,sans-serif" font-size="13" font-weight="600" fill="#1f2530">Hi <tspan fill="#4657d6">Mara Quill!</tspan></text>
      <text x="30" y="52" font-family="Montserrat,sans-serif" font-size="7" fill="#5b6270">Here's Your Report...</text>
      <rect x="30" y="64" width="360" height="150" rx="4" fill="#fff"/>
      <polyline points="50,190 110,170 170,140 230,170 290,130 350,110" fill="none" stroke="#f37521" stroke-width="2"/>
      <g fill="#4657d6"><circle cx="170" cy="140" r="4"/><circle cx="290" cy="130" r="4"/></g>
      <rect x="150" y="98" width="44" height="18" rx="4" fill="#4657d6"/>
      <text x="158" y="111" font-family="Montserrat,sans-serif" font-size="8" font-weight="600" fill="#fff">$ 2352</text>
      <rect x="30" y="224" width="175" height="140" rx="4" fill="#fff"/>
      <text x="40" y="240" font-family="Montserrat,sans-serif" font-size="6" font-weight="600" fill="#5b6270">ANALYTICAL</text>
      <g fill="#e6e9f0"><rect x="40" y="252" width="150" height="3"/><rect x="40" y="264" width="150" height="3"/><rect x="40" y="276" width="150" height="3"/><rect x="40" y="288" width="150" height="3"/><rect x="40" y="300" width="150" height="3"/><rect x="40" y="312" width="150" height="3"/></g>
      <rect x="215" y="224" width="175" height="140" rx="4" fill="#fff"/>
      <text x="225" y="240" font-family="Montserrat,sans-serif" font-size="6" font-weight="600" fill="#5b6270">CALENDAR</text>
      <g fill="#c7ccd8">
        <circle cx="235" cy="262" r="2"/><circle cx="255" cy="262" r="2"/><circle cx="275" cy="262" r="2"/><circle cx="295" cy="262" r="2"/><circle cx="315" cy="262" r="2"/><circle cx="335" cy="262" r="2"/><circle cx="355" cy="262" r="2"/>
        <circle cx="235" cy="280" r="2"/><circle cx="255" cy="280" r="2"/><circle cx="275" cy="280" r="2"/><circle cx="295" cy="280" r="2"/><circle cx="315" cy="280" r="2"/><circle cx="335" cy="280" r="2"/><circle cx="355" cy="280" r="2"/>
        <circle cx="235" cy="298" r="2"/><circle cx="255" cy="298" r="2"/><circle cx="275" cy="298" r="2"/><circle cx="315" cy="298" r="2"/><circle cx="335" cy="298" r="2"/><circle cx="355" cy="298" r="2"/>
        <circle cx="235" cy="316" r="2"/><circle cx="255" cy="316" r="2"/><circle cx="275" cy="316" r="2"/><circle cx="295" cy="316" r="2"/><circle cx="315" cy="316" r="2"/>
      </g>
      <circle cx="295" cy="298" r="4" fill="#4657d6"/>
      <rect x="410" y="20" width="70" height="355" fill="#dfe5fb"/>
      <text x="420" y="110" font-family="Montserrat,sans-serif" font-size="5" fill="#5b6270">Earning</text>
      <text x="420" y="124" font-family="Montserrat,sans-serif" font-size="10" font-weight="700" fill="#4657d6">$ 1554</text>
      <g fill="#fff"><rect x="420" y="150" width="50" height="8" rx="4"/><rect x="420" y="164" width="50" height="8" rx="4"/><rect x="420" y="178" width="50" height="8" rx="4"/></g>
      <g fill="#c7ccd8"><circle cx="430" cy="240" r="9"/><circle cx="430" cy="270" r="9"/><circle cx="430" cy="300" r="9"/></g>
    </symbol>
  </defs>
</svg>

<h1 class="page-title">BANNERS</h1>

<!-- Banner: centered hero -->
<section class="banner" style="top:274px;height:899px;background:linear-gradient(180deg,#263244 0%,#1f2938 100%)">
  <nav class="nav" style="top:52px">
    <div class="brand"><span class="brand-mark"></span>VELORA</div>
    <div class="menu"><span class="active">PRODUCT</span><span>SERVICES</span><span>NEWS</span><span>TEAM</span><span>ABOUT</span></div>
    <div class="cta pill">CONTACT</div>
  </nav>
  <div class="abs" style="top:175px;left:0;width:1200px;text-align:center">
    <div class="h-light">WE HELP CUSTOMER TO</div>
    <div class="h-bold" style="font-size:36px">OPTIMIZE THEIR PROCESSES</div>
    <p class="lede" style="margin-top:10px">Lorem ipsum dolor sit amet, consectetur adipiscing<br>elit, sed do eiusmod tempor incididunt.</p>
  </div>
  <div class="btn abs" style="top:327px;left:524px;width:152px;height:40px;line-height:40px;border-radius:20px">LEARN MORE</div>
  <svg class="abs" style="top:0;left:0" width="1200" height="899" viewBox="0 0 1200 899" aria-hidden="true">
    <path d="M0 640 C260 700 520 800 1200 770 L1200 899 L0 899Z" fill="#fff"/>
  </svg>
  <div class="shot" style="left:235px;top:452px;width:150px;height:285px"><svg viewBox="0 0 150 285"><use href="#side-left"/></svg></div>
  <div class="shot" style="left:820px;top:452px;width:135px;height:285px"><svg viewBox="0 0 135 285"><use href="#side-right"/></svg></div>
  <div class="shot" style="left:384px;top:405px;width:437px;height:342px">
    <svg viewBox="0 0 435 340"><use href="#dash-overview"/><rect width="435" height="18" fill="#f37521"/><g fill="#fff"><circle cx="404" cy="9" r="2"/><circle cx="412" cy="9" r="2"/><circle cx="420" cy="9" r="2"/></g></svg>
  </div>
</section>

<!-- Banner: left text, booking mockups -->
<section class="banner" style="top:1173px;height:672px;background:radial-gradient(ellipse at 50% 60%,#2b3547 0%,#1e2735 70%)">
  <nav class="nav" style="top:38px">
    <div class="brand"><span class="brand-mark"></span>VELORA</div>
    <div class="menu"><span class="active">PRODUCT</span><span>SERVICES</span><span>NEWS</span><span>TEAM</span><span>ABOUT</span></div>
    <div class="cta">CONTACT</div>
  </nav>
  <div class="nav-rule" style="top:98px"></div>
  <div class="abs" style="top:220px;left:117px">
    <div class="h-light">WE HELP CUSTOMER TO</div>
    <div class="h-bold">TO OPTIMIZE THEIR<br>PROCESSES</div>
    <p class="lede" style="margin-top:12px">Lorem ipsum dolor sit amet, consectetur adipiscing<br>elit, sed do eiusmod tempor incididunt.</p>
    <div class="btn" style="margin-top:22px;width:152px;height:42px;line-height:42px">LEARN MORE</div>
  </div>
  <div class="shot" style="left:730px;top:170px;width:330px;height:245px"><svg viewBox="0 0 435 323" preserveAspectRatio="xMidYMin slice"><use href="#dash-overview"/></svg></div>
  <div class="shot" style="left:888px;top:340px;width:210px;height:95px"><svg viewBox="0 0 210 95">
    <rect width="210" height="95" fill="#f6f7fb"/>
    <g><rect x="12" y="14" width="90" height="4" fill="#4657d6"/><rect x="12" y="26" width="80" height="4" fill="#e0474c"/><rect x="12" y="38" width="95" height="4" fill="#4657d6"/><rect x="12" y="50" width="70" height="4" fill="#33c27a"/><rect x="12" y="62" width="85" height="4" fill="#4657d6"/></g>
    <circle cx="160" cy="44" r="22" fill="none" stroke="#dfe5fb" stroke-width="6"/><path d="M140 54 a22 22 0 0 1 34 -28" fill="none" stroke="#3f86d9" stroke-width="6"/>
  </svg></div>
  <div class="shot" style="left:557px;top:157px;width:175px;height:355px;border-radius:16px"><svg viewBox="0 0 175 355"><use href="#phone-booking"/></svg></div>
  <svg class="abs" style="top:0;left:0" width="1200" height="672" viewBox="0 0 1200 672" aria-hidden="true">
    <path d="M560 672 C820 640 1020 600 1200 585 L1200 672Z" fill="#f37521"/>
    <path d="M0 625 C350 690 800 660 1200 640 L1200 672 L0 672Z" fill="#fff"/>
  </svg>
</section>

<!-- Banner: light, orange circle -->
<section class="banner theme-light" style="top:1952px;height:642px;background:var(--light)">
  <svg class="abs" style="top:0;left:0" width="1200" height="642" viewBox="0 0 1200 642" aria-hidden="true">
    <circle cx="1020" cy="150" r="420" fill="#f37521"/>
    <g stroke="#2a2f3a" stroke-width="2" stroke-dasharray="1 9" fill="none"><path d="M632 400 V560 H760"/></g>
  </svg>
  <nav class="nav" style="top:34px">
    <div class="brand"><span class="brand-mark"></span>VELORA</div>
    <div class="menu"><span class="active">PRODUCT</span><span>SERVICES</span><span style="color:#fde3d0">NEWS</span><span style="color:#fde3d0">TEAM</span><span style="color:#fde3d0">ABOUT</span></div>
    <div class="cta solid">CONTACT</div>
  </nav>
  <div class="abs" style="top:203px;left:130px">
    <div class="eyebrow">WELCOME TO VELORA</div>
    <div class="h-light" style="margin-top:14px">WE HELP CUSTOMER TO</div>
    <div class="h-bold">TO OPTIMIZE THEIR<br>PROCESSES</div>
    <p class="lede" style="margin-top:12px">Lorem ipsum dolor sit amet, consectetur adipiscing<br>elit, sed do eiusmod tempor incididunt.</p>
    <div class="btn" style="margin-top:22px;width:162px;height:44px;line-height:44px">LEARN MORE</div>
  </div>
  <div class="shot" style="left:720px;top:120px;width:490px;height:375px;border-radius:10px"><svg viewBox="0 0 480 375" preserveAspectRatio="xMinYMin slice"><use href="#dash-report"/></svg></div>
  <div class="shot" style="left:645px;top:210px;width:180px;height:305px;border-radius:14px"><svg viewBox="0 0 180 305"><use href="#phone-wallet"/></svg></div>
</section>

<!-- Banner: light, angular accents -->
<section class="banner theme-light" style="top:2686px;height:641px;background:var(--light)">
  <svg class="abs" style="top:0;left:0" width="1200" height="641" viewBox="0 0 1200 641" aria-hidden="true">
    <polygon points="618,118 735,235 660,305 618,305" fill="#f37521"/>
    <polygon points="618,300 668,340 618,470" fill="#222c3b"/>
    <g stroke="#2a2f3a" stroke-width="2" stroke-dasharray="1 9" fill="none"><path d="M636 400 V560 H770"/></g>
  </svg>
  <nav class="nav" style="top:34px">
    <div class="brand"><span class="brand-mark"></span>VELORA</div>
    <div class="menu"><span class="active">PRODUCT</span><span>SERVICES</span><span>NEWS</span><span>TEAM</span><span>ABOUT</span></div>
    <div class="cta solid">CONTACT</div>
  </nav>
  <div class="abs" style="top:203px;left:135px">
    <div class="eyebrow">WELCOME TO VELORA</div>
    <div class="h-light" style="margin-top:14px">WE HELP CUSTOMER TO</div>
    <div class="h-bold">TO OPTIMIZE THEIR<br>PROCESSES</div>
    <p class="lede" style="margin-top:12px">Lorem ipsum dolor sit amet, consectetur adipiscing<br>elit, sed do eiusmod tempor incididunt.</p>
    <div class="btn" style="margin-top:22px;width:162px;height:44px;line-height:44px">LEARN MORE</div>
  </div>
  <div class="shot" style="left:726px;top:120px;width:490px;height:375px;border-radius:10px"><svg viewBox="0 0 480 375" preserveAspectRatio="xMinYMin slice"><use href="#dash-report"/></svg></div>
  <div class="shot" style="left:650px;top:210px;width:180px;height:305px;border-radius:14px"><svg viewBox="0 0 180 305"><use href="#phone-wallet"/></svg></div>
</section>

<!-- Banner: photo background with chevron -->
<section class="banner" style="top:3412px;height:744px;background:var(--navy-deep)">
  <div class="abs" role="img" aria-label="Hands working on a laptop that shows an analytics dashboard, dark moody office light" style="left:420px;top:0;width:780px;height:744px;background:radial-gradient(ellipse at 65% 45%,#4a5568 0%,#2c3646 40%,#1b2431 80%)"></div>
  <nav class="nav" style="top:34px;left:140px">
    <div class="brand" style="width:280px"><span class="brand-mark"></span>VELORA</div>
    <div class="menu"><span class="active" style="color:#fff;border-color:#fff">PRODUCT</span><span>SERVICES</span><span>NEWS</span><span>TEAM</span><span>ABOUT</span></div>
    <div class="cta accent">CONTACT</div>
  </nav>
  <div class="nav-rule" style="top:96px"></div>
  <div class="abs" style="top:203px;left:143px">
    <div class="eyebrow">WELCOME TO VELORA</div>
    <div class="h-light" style="margin-top:14px">WE HELP CUSTOMER TO</div>
    <div class="h-bold">TO OPTIMIZE THEIR<br>PROCESSES</div>
    <p class="lede" style="margin-top:12px">Lorem ipsum dolor sit amet, consectetur adipiscing<br>elit, sed do eiusmod tempor incididunt.</p>
    <div class="btn" style="margin-top:22px;width:164px;height:44px;line-height:44px">LEARN MORE</div>
  </div>
  <svg class="abs" style="top:0;left:0" width="1200" height="744" viewBox="0 0 1200 744" aria-hidden="true">
    <polygon points="0,562 600,712 1200,562 1200,744 0,744" fill="#f37521"/>
    <polygon points="0,596 600,728 1200,580 1200,744 0,744" fill="#fff"/>
  </svg>
</section>

<!-- Banner: gradient with booking mockups -->
<section class="banner" style="top:4195px;height:809px;background:linear-gradient(100deg,#1f2836 0%,#2a3242 45%,#b5582a 80%,#f37521 100%)">
  <nav class="nav" style="top:40px;left:107px">
    <div class="brand" style="width:295px"><span class="brand-mark"></span>VELORA</div>
    <div class="menu"><span class="active">PRODUCT</span><span>SERVICES</span><span>NEWS</span><span>TEAM</span><span>ABOUT</span></div>
    <div class="cta">CONTACT</div>
  </nav>
  <div class="abs" style="top:225px;left:104px">
    <div class="h-light">WE HELP CUSTOMER TO</div>
    <div class="h-bold">TO OPTIMIZE THEIR<br>PROCESSES</div>
    <p class="lede" style="margin-top:12px">Lorem ipsum dolor sit amet, consectetur adipiscing<br>elit, sed do eiusmod tempor incididunt.</p>
    <div class="btn" style="margin-top:22px;width:154px;height:42px;line-height:42px">LEARN MORE</div>
  </div>
  <div class="shot" style="left:700px;top:165px;width:345px;height:260px"><svg viewBox="0 0 435 328" preserveAspectRatio="xMidYMin slice"><use href="#dash-overview"/></svg></div>
  <div class="shot" style="left:870px;top:355px;width:210px;height:100px"><svg viewBox="0 0 210 100">
    <rect width="210" height="100" fill="#f6f7fb"/>
    <g><rect x="12" y="14" width="90" height="4" fill="#4657d6"/><rect x="12" y="26" width="80" height="4" fill="#e0474c"/><rect x="12" y="38" width="95" height="4" fill="#4657d6"/><rect x="12" y="50" width="70" height="4" fill="#33c27a"/><rect x="12" y="62" width="85" height="4" fill="#4657d6"/></g>
    <circle cx="160" cy="46" r="22" fill="none" stroke="#dfe5fb" stroke-width="6"/><path d="M140 56 a22 22 0 0 1 34 -28" fill="none" stroke="#3f86d9" stroke-width="6"/>
  </svg></div>
  <div class="shot" style="left:545px;top:157px;width:175px;height:355px;border-radius:16px"><svg viewBox="0 0 175 355"><use href="#phone-booking"/></svg></div>
  <svg class="abs" style="top:0;left:0" width="1200" height="809" viewBox="0 0 1200 809" aria-hidden="true">
    <path d="M0 530 C300 690 700 760 1200 700 L1200 720 C700 775 300 710 0 570Z" fill="#f37521"/>
    <path d="M0 580 C300 720 700 785 1200 730 L1200 809 L0 809Z" fill="#fff"/>
  </svg>
</section>

</div>
</body>
</html>
```